Corvana Tongue Works, LLC

We need a business card that includes information about our business and conveys a reliable business that provides document translation services and interpreters for a variety of corporate and individual clients. We want to come across as professional, reliable, yet approachable. It should include the following on one side:

ESL / ENL Language Classes, Private Lessons, and Online Tutors
PLEXA Training and Testing
Translating & Interpreting Services
Contact us about Over-the-Phone Interpreting in over 200 languages
24/7/365
www.corvanatongue.example

The other side should include (555) 481-3062

Rhoda Pelling, President
482 Garnet Ave., Ste. 219
Indianapolis, IN 40917

Please add USA as part of the address. Also, please add rmpelling@corvanatongueworks.example as the e-mail address. Thank you.

Target Market(s)

Business professionals, their families, the international community

Industry/Entity Type

Business

Contact Information for Business Card

24/7/365
www.corvanatongue.example

(555) 481-3062

Rhoda Pelling, President
482 Garnet Ave., Ste. 219
Indianapolis, IN 40917
USA

Font styles to use
Sans Serif

Colors

Designer to choose colors to be used in the design.

Requirements
Must have
• See project description
• e-mail address and web address
• Phone number
Nice to have
• a globe
• physical address
Should not have
• Should not have the same color scheme as other agencies in our market in Indiana unless it is blue and black. No purple or yellow.

```html
<!DOCTYPE html>
<html lang="en">
<head>
<meta charset="utf-8">
<title>Corvana Tongue Works – Business Card</title>
<link href="https://fonts.googleapis.com/css2?family=Open+Sans:wght@400;600;700&family=Tenor+Sans&display=swap" rel="stylesheet">
<style>
  :root{
    --bg:#e4e4e4;
    --charcoal:#2f3134;
    --charcoal-map:#3a3d41;
    --blue:#1f9ad6;
    --white:#ffffff;
    --ink:#2b2d30;
    --muted:#55585c;
  }
  *{box-sizing:border-box;margin:0;padding:0}
  html,body{width:1200px;height:852px;overflow:hidden;background:var(--bg)}
  body{position:relative;font-family:"Open Sans",Arial,sans-serif}
  .card{position:absolute;top:276px;width:520px;height:300px;border-radius:22px;overflow:hidden;box-shadow:0 6px 18px rgba(0,0,0,.18)}

  /* Back side */
  .card-back{left:50px;background:var(--charcoal);color:var(--white)}
  .card-back .map-area{position:absolute;left:30px;top:25px;width:460px;height:220px;border-radius:40px;
    background:radial-gradient(ellipse at center,var(--charcoal-map) 0%,var(--charcoal) 75%)}
  .services{position:absolute;left:0;right:0;top:48px;text-align:center;font-size:15px;line-height:22px}
  .services .mark{color:var(--blue);font-weight:700;margin-right:4px}
  .services .gap{margin-left:12px}
  .divider{width:220px;height:1px;background:var(--blue);margin:8px auto 8px}
  .callout{font-size:15px;line-height:21px}
  .back-web{position:absolute;left:0;right:0;bottom:22px;text-align:center;font-size:14px;letter-spacing:.3px}
  .back-web .accent{color:var(--blue)}

  /* Front side */
  .card-front{left:630px;background:var(--white);color:var(--ink)}
  .card-front svg.shapes{position:absolute;inset:0}
  .company{position:absolute;left:26px;top:26px;font-family:"Tenor Sans","Open Sans",sans-serif;font-size:25px;line-height:34px;color:var(--ink);letter-spacing:.2px;white-space:nowrap}
  .person{position:absolute;left:26px;top:150px;color:var(--white)}
  .person .name{font-size:19px;font-weight:700}
  .person .title{font-size:12px;margin-left:8px;opacity:.9}
  .contacts{position:absolute;left:26px;top:180px;list-style:none;color:var(--white);font-size:13px;line-height:19px}
  .contacts li{display:flex;align-items:center;gap:10px;white-space:nowrap}
  .contacts svg{width:12px;height:12px;fill:var(--white);flex:none}
  .address{position:absolute;left:26px;top:252px;font-size:13px;line-height:18px;color:var(--muted)}
</style>
</head>
<body>

<section class="card card-back" aria-label="Card back">
  <div class="map-area" role="img" aria-label="Faint world map in the background"></div>
  <div class="services">
    <p><span class="mark">»</span>ESL / ENL Language Classes</p>
    <p><span class="mark">»</span>Private Lessons <span class="mark gap">»</span>Online Tutors</p>
    <p><span class="mark">»</span>PLEXA Training and Testing</p>
    <p><span class="mark">»</span>Translating &amp; Interpreting Services</p>
    <div class="divider"></div>
    <p class="callout">Contact us about Over-the-Phone</p>
    <p class="callout">Interpreting in over 200 languages</p>
    <p class="callout">24/7/365</p>
  </div>
  <p class="back-web">www.<span class="accent">corvanatongue</span>.example</p>
</section>

<section class="card card-front" aria-label="Card front">
  <svg class="shapes" width="520" height="300" viewBox="0 0 520 300" aria-hidden="true">
    <polygon points="0,140 300,140 330,96 520,96 520,160 385,160 335,242 0,242" fill="var(--charcoal)"/>
    <circle cx="432" cy="126" r="60" fill="var(--blue)" stroke="var(--white)" stroke-width="7"/>
  </svg>
  <p class="company">Corvana Tongue Works, LLC</p>
  <p class="person"><span class="name">Rhoda Pelling</span><span class="title">| President</span></p>
  <ul class="contacts">
    <li><svg viewBox="0 0 24 24"><path d="M6.6 10.8a15 15 0 006.6 6.6l2.2-2.2a1 1 0 011-.25 11.4 11.4 0 003.6.6 1 1 0 011 1V20a1 1 0 01-1 1A17 17 0 013 4a1 1 0 011-1h3.5a1 1 0 011 1c0 1.25.2 2.45.6 3.6a1 1 0 01-.25 1z"/></svg>(555) 481-3062</li>
    <li><svg viewBox="0 0 24 24"><path d="M2 5h20v14H2z M3 6l9 7 9-7" stroke="#2f3134" stroke-width="1.5"/></svg>rmpelling@corvanatongueworks.example</li>
    <li><svg viewBox="0 0 24 24"><circle cx="12" cy="12" r="10"/></svg>www.corvanatongue.example</li>
  </ul>
  <p class="address">482 Garnet Ave., Ste. 219<br>Indianapolis, IN 40917 USA</p>
</section>

</body>
</html>
```